Business Card for premium dental clinic

We are a premium dental clinic based in Brasov, Romania with more than 15 year on the market, providing quality dental treatment made by a team of more specialized dentists, working with modern equipment as a solution to beautiful and healthy teeth.

Our current logo for the clinic use 2 square with colors black and gold - dr Ternisu - studio, using family fonts Bodoni, Myriad Pro and Segoe Print.
Depending on the printing we used some gold CMYK background or gold foil picture background or a gold gradient.
We want a business card:
- eye catching business card
- distinguished business card
- premium design
- to keep the color scheme of black and gold
- to attract the customers to spent time reading the information
- modern concept

```html
<!DOCTYPE html>
<html lang="en">
<head>
<meta charset="utf-8">
<title>Aurea Dental Clinic – Business Card</title>
<link rel="stylesheet" href="https://fonts.googleapis.com/css2?family=Montserrat:wght@500;600;700&display=swap">
<style>
  :root {
    --backdrop: #3a302a;
    --card: #38383a;
    --card-deep: #2f2f31;
    --emboss: #1f1f21;
    --gold: #d4a43a;
    --gold-light: #f0cf6e;
    --gold-dark: #a8781e;
    --white: #ffffff;
    --rule: #bdbdbd;
  }
  * { box-sizing: border-box; margin: 0; padding: 0; }
  html, body { width: 1200px; height: 800px; overflow: hidden; }
  body {
    background: var(--backdrop);
    font-family: "Montserrat", Arial, sans-serif;
    position: relative;
  }
  .card {
    position: absolute;
    top: 257px;
    width: 500px;
    height: 286px;
    background: var(--card);
    border: 2px solid var(--gold);
    border-radius: 4px;
    box-shadow: 0 10px 30px rgba(0,0,0,.35);
  }
  .card--back { left: 70px; }
  .card--front { left: 630px; }

  .brand {
    font-weight: 500;
    line-height: 1.05;
  }
  .card--back .brand {
    position: absolute;
    left: 0; right: 0; top: 88px;
    text-align: center;
    color: var(--emboss);
    font-size: 64px;
  }
  .card--back .brand small {
    display: block;
    font-size: 16px;
    letter-spacing: 3px;
    margin-top: 8px;
  }

  .card--front .brand {
    position: absolute;
    left: 34px; top: 96px;
    color: var(--gold);
    font-size: 46px;
  }
  .card--front .brand small {
    display: block;
    font-size: 11px;
    letter-spacing: 2.2px;
    margin-top: 6px;
  }

  .divider {
    position: absolute;
    left: 268px; top: 60px;
    width: 1px; height: 160px;
    background: var(--rule);
  }
  .contact {
    position: absolute;
    left: 286px; top: 62px;
    font-size: 13px;
    font-weight: 500;
    color: var(--gold);
  }
  .contact__name {
    color: var(--white);
    font-size: 19px;
    font-weight: 700;
  }
  .contact__role { font-size: 12px; margin-bottom: 8px; }
  .contact__address { line-height: 1.3; margin-bottom: 10px; }
  .contact__line {
    display: flex;
    align-items: center;
    gap: 8px;
    height: 22px;
  }
  .contact__line svg { width: 12px; height: 12px; fill: var(--white); flex: none; }
</style>
</head>
<body>
  <section class="card card--back" aria-label="Card back">
    <div class="brand">Aurea<small>DENTAL CLINIC</small></div>
  </section>

  <section class="card card--front" aria-label="Card front">
    <div class="brand">Aurea<small>DENTAL CLINIC</small></div>
    <div class="divider"></div>
    <div class="contact">
      <div class="contact__name">Mara Ionescu</div>
      <div class="contact__role">Manager</div>
      <div class="contact__address">Str. Lunga 12,<br>Brasov 500035</div>
      <div class="contact__line">
        <svg viewBox="0 0 24 24" aria-hidden="true"><path d="M6.6 10.8a15 15 0 0 0 6.6 6.6l2.2-2.2c.3-.3.7-.4 1-.2 1.1.4 2.3.6 3.6.6.6 0 1 .4 1 1V20c0 .6-.4 1-1 1A17 17 0 0 1 3 4c0-.6.4-1 1-1h3.5c.6 0 1 .4 1 1 0 1.3.2 2.5.6 3.6.1.3 0 .7-.2 1z"/></svg>
        <span>123-555-0147</span>
      </div>
      <div class="contact__line">
        <svg viewBox="0 0 24 24" aria-hidden="true"><path d="M2 5h20v14H2zm2 2v.5l8 5 8-5V7zm0 3v7h16v-7l-8 5z"/></svg>
        <span>hello@aureadental.ro</span>
      </div>
      <div class="contact__line">
        <svg viewBox="0 0 24 24" aria-hidden="true"><path d="M12 2a10 10 0 1 0 0 20 10 10 0 0 0 0-20zm0 2c.9 0 2.2 2 2.7 5H9.3C9.8 6 11.1 4 12 4zM4.3 11h3a20 20 0 0 0 0 2h-3a8 8 0 0 1 0-2zm5 0h5.4a18 18 0 0 1 0 2H9.3a18 18 0 0 1 0-2zm7.4 0h3a8 8 0 0 1 0 2h-3a20 20 0 0 0 0-2zM9.3 15h5.4c-.5 3-1.8 5-2.7 5s-2.2-2-2.7-5z"/></svg>
        <span>www.aureadental.ro</span>
      </div>
    </div>
  </section>
</body>
</html>
```